Modern Verdell Tree Care Website

I need a website for a full service Tree Care company. The company provides tree pruning, tree removal, tree preservation, emergency services, stump grinding, and emergency tree services.

Target Market(s)

Customers that need tree services

Industry/Entity Type

Landscaping, Tree Services

Coding

Coded - Design and coding required

Number of Pages Required

5+ page

Font styles to use
Sans Serif

Requirements
Must have
• Good clean design that showcases the services the company provides.
Nice to have
• Services page; contact form, blog, home page, about page

```html
<!DOCTYPE html>
<html lang="en">
<head>
<meta charset="utf-8">
<title>Verdell Tree Care</title>
<link rel="stylesheet" href="https://fonts.googleapis.com/css2?family=Fira+Sans:wght@400;500;600&family=Open+Sans:wght@400;600&display=swap">
<style>
:root{
  --green:#7bbf3a;
  --green-dark:#5f9a26;
  --orange:#f6a22c;
  --navy:#13204a;
  --footer:#0e1436;
  --grey-bar:#5b6064;
  --text:#7a7f87;
  --light:#f6f6f6;
  --dark:#26282a;
}
*{margin:0;padding:0;box-sizing:border-box}
html,body{width:1200px;height:4186px;overflow:hidden}
body{position:relative;background:#fff;font-family:"Open Sans",sans-serif;color:var(--text)}
.abs{position:absolute}
h1,h2,h3,h4,.head{font-family:"Fira Sans",sans-serif}

/* header */
.topbar{left:490px;top:0;width:710px;height:32px;background:var(--grey-bar);color:#fff;font-size:12px;display:flex;align-items:center;gap:30px;padding-left:95px}
.topbar-wedge{left:460px;top:0}
.topbar span{display:flex;align-items:center;gap:10px}
.ico-ring{width:22px;height:22px;border:1.5px solid #fff;border-radius:50%;display:inline-flex;align-items:center;justify-content:center}
.brand{left:141px;top:24px;display:flex;align-items:center;gap:12px}
.brand-mark{width:50px;height:50px;background:var(--green)}
.brand-name{font-family:"Fira Sans",sans-serif;font-weight:600;font-size:26px;color:var(--grey-bar);line-height:1}
.nav{left:496px;top:54px;display:flex;font-size:12px;color:#222;font-family:"Fira Sans",sans-serif}
.nav a{color:inherit;text-decoration:none;position:absolute;white-space:nowrap}
.nav .active{color:var(--green)}
.nav .active::after{content:"";position:absolute;left:-6px;right:-6px;top:30px;height:3px;background:var(--green)}
.socials{left:920px;top:50px;display:flex;gap:16px}
.soc{width:24px;height:24px;border:1.5px solid #1c3c8c;border-radius:50%}

/* hero */
.hero-photo{left:0;top:90px;width:1200px;height:723px;background:linear-gradient(100deg,#0b0c0a 0%,#1d2118 35%,#4a5136 60%,#6b7048 80%,#3e4230 100%)}
.hero-tag{left:122px;top:281px;width:265px;height:43px;background:rgba(120,125,125,.55);border-left:4px solid var(--green);color:#fff;font:500 21px "Fira Sans",sans-serif;padding:8px 0 0 18px}
.hero-title{left:118px;top:335px;font:600 66px "Fira Sans",sans-serif;color:#fff}
.hero-text{left:122px;top:424px;width:430px;font-size:17px;line-height:26px;color:#fff}
.btn{background:var(--green);color:#fff;font:600 16px "Fira Sans",sans-serif;display:flex;align-items:center;justify-content:center;gap:12px}
.hero-btn{left:122px;top:523px;width:174px;height:49px}

/* about */
.about-photo{left:220px;top:878px;width:317px;height:455px;background:linear-gradient(180deg,#eef0f2,#d4d8dc);border-radius:4px}
.label{font-size:12px;color:var(--green);text-transform:uppercase;padding-bottom:3px;border-bottom:1.5px solid var(--green);display:inline-block}
.about-label{left:610px;top:902px}
.h2{color:var(--navy);font-weight:500;font-size:38px;line-height:48px}
.about-h{left:610px;top:933px}
.about-sub{left:610px;top:1052px;font:500 19px "Fira Sans",sans-serif;color:var(--navy)}
.about-p{left:610px;width:455px;font-size:12px;line-height:19px}
.contact-btn{left:610px;top:1224px;width:135px;height:39px;font-size:14px}

/* services */
.services-bg{left:0;top:1333px;width:1200px;height:553px}
.srv-label{left:0;width:1200px;top:1398px;text-align:center;color:#fff;font-size:13px}
.srv-label span{border-bottom:1px solid #fff;padding-bottom:3px}
.srv-h{left:0;width:1200px;top:1430px;text-align:center;color:#fff;font:500 43px "Fira Sans",sans-serif}
.card{background:#fff;text-align:center;padding-top:28px}
.card .circle{width:82px;height:82px;border-radius:50%;background:var(--green);margin:0 auto;display:flex;align-items:center;justify-content:center}
.card h3{font-weight:600;font-size:18px;color:#222;margin-top:32px}
.card p{font-size:13px;line-height:21px;margin:8px auto 0;width:210px}
.card.active{background:rgba(123,191,58,.92)}
.card.active .circle{background:#fff}
.card.active h3,.card.active p{color:#fff}

/* why */
.why-photo{left:211px;top:1910px;width:293px;height:614px;background:linear-gradient(180deg,#e4a070 0%,#c9cdd2 25%,#6e7a88 60%,#9a7040 100%);border-radius:4px 4px 0 0}
.why-label{left:616px;top:1985px}
.why-h{left:616px;top:2021px;font-size:42px;line-height:52px}
.feat{width:220px;height:99px;background:#fff;box-shadow:0 2px 10px rgba(0,0,0,.07);padding:18px 0 0 66px}
.feat svg{position:absolute;left:18px;top:20px}
.feat h4{font-weight:500;font-size:16px;color:#2c6c8a}
.feat p{font-size:12px;line-height:20px;margin-top:4px;width:140px}

/* appointment */
.appt-bg{left:0;top:2524px;width:1200px;height:508px}
.appt-h{left:130px;top:2612px;color:#fff;font:500 35px "Fira Sans",sans-serif}
.field{background:#fff;width:231px;height:43px;border:1px solid #ccc;font-size:14px;color:#333;display:flex;align-items:center;gap:9px;padding-left:16px}
.field.msg{height:111px;align-items:flex-start;padding-top:13px}
.appt-btn{left:132px;top:2886px;width:130px;height:36px;font-size:12px;font-weight:400}
.appt-photo{left:683px;top:2463px;width:455px;height:482px;background:linear-gradient(180deg,#e9eaec 0%,#c8d4e0 30%,#d8e46a 55%,#2a3a5c 90%);border-radius:6px 6px 0 0}

/* steps */
.steps-bg{left:0;top:2900px;width:1200px;height:932px;background:var(--light)}
.steps-label{left:0;width:1200px;top:3157px;text-align:center}
.steps-h{left:0;width:1200px;top:3188px;text-align:center;font-size:43px}
.step{width:220px;height:220px;border-radius:50%;background:#fff;box-shadow:0 3px 12px rgba(0,0,0,.08);text-align:center}
.step .icon{position:absolute;left:53px;top:-94px;width:114px;height:114px;border-radius:50%;background:var(--green);display:flex;align-items:center;justify-content:center;border:6px solid #fff}
.step .num{position:absolute;left:0;width:100%;top:25px;font-size:13px;color:var(--green);font-weight:600}
.step h4{margin-top:55px;font-weight:600;font-size:15px;color:#2c6c8a}
.step p{font-size:10px;line-height:13px;width:170px;margin:10px auto 0;color:#333}
.step a{display:block;margin-top:11px;font-size:10px;color:#2c6c8a;text-decoration:none}
.step.active{background:var(--green)}
.step.active .icon{background:#fff;border-color:#fff}
.step.active h4,.step.active p,.step.active a,.step.active .num{color:#fff}

/* footer */
.footer-bg{left:0;top:3691px;width:1200px;height:495px}
.f-brand{left:0;width:1200px;top:3842px;display:flex;justify-content:center;align-items:center;gap:16px;color:#fff}
.f-brand .brand-mark{background:#fff;width:58px;height:58px}
.f-brand .brand-name{color:#fff;font-size:36px}
.f-nav{top:3949px;color:#fff;font-size:15px;font-family:"Fira Sans",sans-serif}
.f-nav a{position:absolute;color:#fff;text-decoration:none;white-space:nowrap}
.f-line{left:141px;top:4002px;width:918px;height:1px;background:rgba(255,255,255,.3)}
.f-item{display:flex;align-items:center;gap:12px;color:#fff;font-size:12px;line-height:18px}
.f-ring{width:56px;height:56px;border-radius:50%;border:1.5px solid #fff;display:flex;align-items:center;justify-content:center}
.f-item b{font-weight:400;font-size:14px}
.f-div{width:1px;height:62px;background:rgba(255,255,255,.35);top:4042px}
.bottom-bar{left:0;top:4132px;width:1200px;height:54px;background:var(--green)}
.bottom-name{left:146px;top:4151px;color:#fff;font-size:13px}
.bsoc{width:26px;height:26px;border:1px solid #fff;top:4146px}
</style>
</head>
<body>

<!-- Header -->
<svg class="abs topbar-wedge" width="60" height="32" viewBox="0 0 60 32" aria-hidden="true"><path d="M0 0H60V32H30Z" fill="#5b6064"/></svg>
<div class="abs topbar">
  <span><span class="ico-ring"><svg width="11" height="11" viewBox="0 0 24 24"><path d="M6.6 10.8a15 15 0 006.6 6.6l2.2-2.2a1 1 0 011-.25 11 11 0 003.6.6 1 1 0 011 1V20a1 1 0 01-1 1A17 17 0 013 4a1 1 0 011-1h3.5a1 1 0 011 1 11 11 0 00.6 3.6 1 1 0 01-.25 1z" fill="#fff"/></svg></span>CALL US TODAY : (555) 214-0387</span>
  <span><span class="ico-ring"><svg width="11" height="9" viewBox="0 0 24 18"><rect x="1" y="1" width="22" height="16" fill="none" stroke="#fff" stroke-width="2"/><path d="M1 1l11 9 11-9" fill="none" stroke="#fff" stroke-width="2"/></svg></span>EMAIL: info@verdelltrees.com</span>
</div>
<div class="abs brand"><div class="brand-mark"></div><div class="brand-name">Verdell Tree Care</div></div>
<nav class="abs nav">
  <a class="active" style="left:0">HOME</a>
  <a style="left:94px">Solutions</a>
  <a style="left:189px">About Us</a>
  <a style="left:283px">Giving Back</a>
  <a style="left:374px">Login</a>
</nav>
<div class="abs socials"><span class="soc"></span><span class="soc"></span><span class="soc"></span><span class="soc"></span></div>

<!-- Hero -->
<div class="abs hero-photo" role="img" aria-label="Arborist in harness cutting a large tree trunk"></div>
<svg class="abs" style="left:0;top:690px" width="1200" height="130" viewBox="0 0 1200 130" aria-hidden="true">
  <path d="M0 40 C300 120 700 140 1200 10 V130 H0Z" fill="#fff"/>
  <path d="M0 36 C260 105 560 120 1200 0 V18 C620 118 300 125 0 40Z" fill="#7bbf3a"/>
  <path d="M180 95 C520 140 860 110 1200 40 V58 C860 130 520 150 180 95Z" fill="#f6a22c"/>
</svg>
<div class="abs hero-tag">We are experts in</div>
<h1 class="abs hero-title">Tree Care</h1>
<p class="abs hero-text">Lorem ipsum dolor sit amet, consectetur adipiscing elit, sed do eiusmod tempor incididunt ut labore et dolore magna aliqua.</p>
<div class="abs btn hero-btn">Read More</div>

<!-- About -->
<div class="abs about-photo" role="img" aria-label="Three business people shaking hands"></div>
<div class="abs label about-label">Who we are</div>
<h2 class="abs h2 about-h">We Offer Sustainable<br>Tree Solutions</h2>
<div class="abs about-sub">Enhancing Landscapes, One Tree at a Time</div>
<p class="abs about-p" style="top:1092px">Lorem ipsum dolor sit amet, consectetur adipiscing elit, sed do eiusmod temp or incididunt ut labore et dolore magna aliqua. Ut enim ad minim veniam, quis laboris nisi ut aliquip ex ea commodo consequat.</p>
<p class="abs about-p" style="top:1160px">Lorem ipsum dolor sit amet, consectetur adipiscing elit, sed do eiusmod temp or incididunt ut labore et dolore magna aliqua.</p>
<div class="abs btn contact-btn">Contact us <svg width="16" height="10" viewBox="0 0 16 10"><path d="M0 5h14M10 1l4 4-4 4" stroke="#fff" fill="none" stroke-width="1.5"/></svg></div>

<!-- Services -->
<svg class="abs services-bg" viewBox="0 0 1200 553" role="img" aria-label="Dark forest canopy background">
  <defs><linearGradient id="forest" x1="0" y1="0" x2="1" y2="1"><stop offset="0" stop-color="#1e201d"/><stop offset=".5" stop-color="#3a3d36"/><stop offset="1" stop-color="#24261f"/></linearGradient></defs>
  <path d="M0 70 C300 10 900 0 1200 60 V553 H0Z" fill="url(#forest)"/>
</svg>
<div class="abs srv-label"><span>OUR SERVICES</span></div>
<h2 class="abs srv-h">Services We Provide</h2>
<div class="abs card" style="left:164px;top:1538px;width:290px;height:267px">
  <div class="circle"><svg width="40" height="40" viewBox="0 0 40 40" fill="none" stroke="#fff" stroke-width="2"><circle cx="20" cy="22" r="15"/><path d="M20 22l6-8M11 22h3M26 22h3M20 11v3"/></svg></div>
  <h3>Tree Pruning</h3><p>Lorem ipsum dolor sit amet, con sectetur adipiscing elit, sed do eiusmod tem</p>
</div>
<div class="abs card active" style="left:454px;top:1520px;width:286px;height:301px;padding-top:46px">
  <div class="circle"><svg width="40" height="40" viewBox="0 0 40 40" fill="none" stroke="#7bbf3a" stroke-width="2"><path d="M20 7l13 9-5 15H12L7 16z"/><circle cx="20" cy="7" r="3" fill="#fff"/><circle cx="33" cy="16" r="3" fill="#fff"/><circle cx="28" cy="31" r="3" fill="#fff"/><circle cx="12" cy="31" r="3" fill="#fff"/><circle cx="7" cy="16" r="3" fill="#fff"/></svg></div>
  <h3>Tree Removal</h3><p>Lorem ipsum dolor sit amet, con sectetur adipiscing elit, sed do eiusmod tem</p>
</div>
<div class="abs card" style="left:740px;top:1538px;width:286px;height:267px">
  <div class="circle"><svg width="40" height="40" viewBox="0 0 40 40" fill="none" stroke="#fff" stroke-width="2"><path d="M8 32h24M12 32c0-6 4-9 9-9M16 23l10-14 4 3-10 13"/></svg></div>
  <h3>Stump Grinding</h3><p>Lorem ipsum dolor sit amet, con sectetur adipiscing elit, sed do eiusmod tem</p>
</div>

<!-- Why choose -->
<div class="abs why-photo" role="img" aria-label="Construction worker in orange hard hat and tool belt"></div>
<div class="abs label why-label">Why choose us</div>
<h2 class="abs h2 why-h">Your Partner in Tree<br>Presevation</h2>
<div class="abs feat" style="left:602px;top:2151px"><svg width="32" height="32" viewBox="0 0 40 40" fill="none" stroke="#7bbf3a" stroke-width="2"><path d="M8 32h24M12 32c0-6 4-9 9-9M16 23l10-14 4 3-10 13"/></svg><h4>Expertise</h4><p>Inventore veritasis uas vitae dicta sunt</p></div>
<div class="abs feat" style="left:847px;top:2151px"><svg width="32" height="32" viewBox="0 0 40 40" fill="none" stroke="#7bbf3a" stroke-width="2"><path d="M8 32h24M12 32c0-6 4-9 9-9M16 23l10-14 4 3-10 13"/></svg><h4>Client-centric</h4><p>Inventore veritasis uas vitae dicta sunt</p></div>
<div class="abs feat" style="left:602px;top:2276px"><svg width="32" height="32" viewBox="0 0 40 40" fill="none" stroke="#7bbf3a" stroke-width="2"><path d="M8 32h24M12 32c0-6 4-9 9-9M16 23l10-14 4 3-10 13"/></svg><h4>Professionalism</h4><p>Inventore veritasis uas vitae dicta sunt</p></div>
<div class="abs feat" style="left:847px;top:2276px"><svg width="32" height="32" viewBox="0 0 40 40" fill="none" stroke="#7bbf3a" stroke-width="2"><path d="M8 32h24M12 32c0-6 4-9 9-9M16 23l10-14 4 3-10 13"/></svg><h4>Proven Record</h4><p>Inventore veritasis uas vitae dicta sunt</p></div>

<!-- Steps background (sits beneath the appointment curve) -->
<div class="abs steps-bg"></div>

<!-- Appointment -->
<svg class="abs appt-bg" viewBox="0 0 1200 508" role="img" aria-label="Dark field at dusk background">
  <defs><linearGradient id="field" x1="0" y1="0" x2="0" y2="1"><stop offset="0" stop-color="#2a2c2b"/><stop offset=".55" stop-color="#333631"/><stop offset="1" stop-color="#1f2a18"/></linearGradient></defs>
  <path d="M0 0H1200V420 C900 500 350 510 0 440Z" fill="url(#field)"/>
</svg>
<div class="abs appt-photo" role="img" aria-label="Two smiling engineers in hard hats and safety vests holding plans"></div>
<h2 class="abs appt-h">Request An Appointment</h2>
<div class="abs field" style="left:132px;top:2689px"><svg width="14" height="14" viewBox="0 0 16 16" fill="none" stroke="#333"><circle cx="8" cy="5" r="3"/><path d="M2 15c0-4 3-6 6-6s6 2 6 6"/></svg>Full Name</div>
<div class="abs field" style="left:390px;top:2689px"><svg width="14" height="14" viewBox="0 0 16 16" fill="none" stroke="#333"><rect x="1" y="2" width="14" height="12"/><circle cx="8" cy="7" r="2"/><path d="M4 12c1-2 7-2 8 0"/></svg>Email Address</div>
<div class="abs field" style="left:132px;top:2756px"><svg width="14" height="14" viewBox="0 0 24 24" fill="none" stroke="#333" stroke-width="1.8"><path d="M6.6 10.8a15 15 0 006.6 6.6l2.2-2.2 4.6 1.4V20A17 17 0 013 4h3.5l1.4 4.6z"/></svg>Phone</div>
<div class="abs field msg" style="left:390px;top:2756px"><svg width="14" height="14" viewBox="0 0 16 16" fill="none" stroke="#333"><rect x="1" y="3" width="14" height="10"/><path d="M1 3l7 6 7-6"/></svg>Message</div>
<div class="abs field" style="left:132px;top:2824px"><svg width="14" height="14" viewBox="0 0 16 16" fill="none" stroke="#333"><circle cx="8" cy="9" r="6"/><path d="M8 9l3-3"/></svg>Date</div>
<div class="abs btn appt-btn">Request Now →</div>

<!-- Steps -->
<div class="abs steps-label"><span class="label">Steps to take</span></div>
<h2 class="abs h2 steps-h">Steps to Take</h2>
<div class="abs step" style="left:123px;top:3336px">
  <div class="icon"><svg width="44" height="44" viewBox="0 0 40 40" fill="none" stroke="#fff" stroke-width="2"><path d="M8 32h24M12 32c0-6 4-9 9-9M16 23l10-14 4 3-10 13"/></svg></div>
  <div class="num">1</div><h4>Get in touch with us</h4>
  <p>Lorem ipsum dolor sit amet, con sectetur adipiscing elit, sed do eiusmod tempor incididunt ut labore et dol ore magna aliqua. Ut</p><a>Read More</a>
</div>
<div class="abs step active" style="left:366px;top:3336px">
  <div class="icon"><svg width="44" height="44" viewBox="0 0 40 40" fill="none" stroke="#7bbf3a" stroke-width="2"><path d="M20 7l13 9-5 15H12L7 16z"/><circle cx="20" cy="7" r="3" fill="#fff"/><circle cx="33" cy="16" r="3" fill="#fff"/><circle cx="28" cy="31" r="3" fill="#fff"/><circle cx="12" cy="31" r="3" fill="#fff"/><circle cx="7" cy="16" r="3" fill="#fff"/></svg></div>
  <div class="num">2</div><h4>Speak to an Expert</h4>
  <p>Lorem ipsum dolor sit amet, con sectetur adipiscing elit, sed do eiusmod tempor incididunt ut labore et dol ore magna aliqua. Ut</p><a>Read More</a>
</div>
<div class="abs step" style="left:614px;top:3336px">
  <div class="icon"><svg width="44" height="44" viewBox="0 0 40 40" fill="none" stroke="#fff" stroke-width="2"><circle cx="20" cy="22" r="15"/><path d="M20 22l6-8M11 22h3M26 22h3M20 11v3"/></svg></div>
  <div class="num">3</div><h4>Schedule a meeting</h4>
  <p>Lorem ipsum dolor sit amet, con sectetur adipiscing elit, sed do eiusmod tempor incididunt ut labore et dol ore magna aliqua. Ut</p><a>Read More</a>
</div>
<div class="abs step" style="left:859px;top:3336px">
  <div class="icon"><svg width="44" height="44" viewBox="0 0 40 40" fill="none" stroke="#fff" stroke-width="2"><circle cx="18" cy="18" r="12"/><path d="M6 18h24M18 6c-5 6-5 18 0 24M18 6c5 6 5 18 0 24"/><circle cx="29" cy="29" r="5"/></svg></div>
  <div class="num">4</div><h4>Start Sessions</h4>
  <p>Lorem ipsum dolor sit amet, con sectetur adipiscing elit, sed do eiusmod tempor incididunt ut labore et dol ore magna aliqua. Ut</p><a>Read More</a>
</div>

<!-- Footer -->
<svg class="abs footer-bg" viewBox="0 0 1200 495" aria-hidden="true">
  <path d="M0 98 C350 20 800 10 1200 70 V495 H0Z" fill="#0e1436"/>
  <path d="M0 90 C380 0 800 -10 1200 50 V75 C800 10 380 20 0 98Z" fill="#7bbf3a"/>
  <path d="M80 70 C420 -5 820 -15 1200 20 V38 C820 0 420 15 80 70Z" fill="#f6a22c"/>
</svg>
<div class="abs f-brand"><div class="brand-mark"></div><div class="brand-name">Verdell Tree Care</div></div>
<div class="abs f-nav">
  <a style="left:296px">HOME</a><a style="left:390px">SERVICES</a><a style="left:496px">ABOUT US</a><a style="left:615px">TESTIMONIALS</a><a style="left:764px">BLOG</a>
</div>
<div class="abs f-line"></div>
<div class="abs f-item" style="left:141px;top:4045px"><div class="f-ring"><svg width="30" height="30" viewBox="0 0 30 30" fill="none" stroke="#fff" stroke-width="1.5"><circle cx="15" cy="15" r="12"/><path d="M3 15h24M15 3c-6 7-6 17 0 24M15 3c6 7 6 17 0 24"/></svg></div><div>48 Larchmont Way,<br>Brookfield, OR 97415</div></div>
<div class="abs f-div" style="left:398px"></div>
<div class="abs f-item" style="left:474px;top:4045px"><div class="f-ring"><svg width="26" height="30" viewBox="0 0 26 30" fill="none" stroke="#fff" stroke-width="1.5"><rect x="6" y="3" width="13" height="24" rx="2"/><path d="M11 23h3"/></svg></div><div><b>PHONE</b><br>(555) 214 0387</div></div>
<div class="abs f-div" style="left:719px"></div>
<div class="abs f-item" style="left:796px;top:4045px"><div class="f-ring"><svg width="30" height="30" viewBox="0 0 30 30" fill="none" stroke="#fff" stroke-width="1.5"><path d="M4 12l11-8 11 8v14H4z"/><path d="M4 12l11 8 11-8"/></svg></div><div><b>EMAIL</b><br>info@verdelltrees.com</div></div>
<div class="abs bottom-bar"></div>
<div class="abs bottom-name">Verdell Tree Care</div>
<div class="abs bsoc" style="left:935px"></div>
<div class="abs bsoc" style="left:968px"></div>
<div class="abs bsoc" style="left:1001px"></div>
<div class="abs bsoc" style="left:1034px"></div>

</body>
</html>
```